Ledgerline Code Works business card design.

We are a software development company that develop Software for finance companies and related industries.

We need a 2 sided business card designed. We have a new logo already designed (see attached eps and ai) We are after a clean simple corporate look. One side with just our logo, and the second side with our details.

Greg Halvorsen
Managing Director

Suite 5 Level 8, 147 Marlow Street Sydney NSW 2000

Direct: +61 2 9387 4625
Mobile: +61 4 1736 8490
Email: gregh@lcw.net.au
Web: www.lcw.net.au

I have included 2 logo files an .ai and .eps. I noticed that the lines either side of the partners looks a bit jaggered and needs to be made sharper.

I would like to introduce a little colour somewhere rather than having it all black and white. But not over the top, keeping with a simple clean corporate look. Perhaps a light blue on some of the text?

If you have other ideas would be pleased to review

Regards

Greg H.

```html
<!DOCTYPE html>
<html lang="en">
<head>
<meta charset="utf-8">
<title>Ledgerline Code Works — Business Card</title>
<link href="https://fonts.googleapis.com/css2?family=Open+Sans:wght@400;600;700&display=swap" rel="stylesheet">
<style>
  :root {
    --stage: #e9e9eb;
    --ink: #141414;
    --card-black: #0b0b0c;
    --card-black-soft: #2a2a2d;
    --paper: #ffffff;
    --sky: #8cc8ec;
    --sky-deep: #3a8fd6;
    --muted: #3c3c3c;
    --white: #ffffff;
  }
  * { box-sizing: border-box; margin: 0; padding: 0; }
  html, body {
    width: 1200px; height: 913px; overflow: hidden;
    background: var(--stage);
    font-family: "Open Sans", Arial, sans-serif;
  }
  .stage { position: relative; width: 1200px; height: 913px; }

  .card {
    position: absolute; top: 297px;
    width: 520px; height: 318px;
    border-radius: 4px; overflow: hidden;
    box-shadow: 0 10px 28px rgba(0,0,0,.18);
  }

  /* Front: logo only */
  .card-front {
    left: 60px;
    background: linear-gradient(135deg, var(--card-black-soft) 0%, var(--card-black) 55%, #000 100%);
    display: flex; align-items: center; justify-content: center;
  }
  .brand {
    display: flex; align-items: center; gap: 12px;
    font-weight: 700; font-size: 21px; letter-spacing: 1.5px;
    text-transform: uppercase; white-space: nowrap;
  }
  .brand-mark { width: 26px; height: 26px; flex: none; }
  .card-front .brand { color: var(--white); }
  .card-front .brand-mark { background: var(--white); }

  /* Back: details */
  .card-back { left: 620px; background: var(--paper); }
  .card-back .swoosh { position: absolute; inset: 0; width: 520px; height: 318px; }
  .card-back .brand {
    position: absolute; left: 30px; top: 150px;
    font-size: 15px; letter-spacing: 1px; gap: 10px; color: var(--ink);
  }
  .card-back .brand-mark { width: 18px; height: 18px; background: var(--ink); }

  .person { position: absolute; right: 24px; top: 16px; text-align: right; }
  .person-name { color: var(--sky); font-size: 14px; font-weight: 600; line-height: 18px; }
  .person-role { color: var(--muted); font-size: 10.5px; line-height: 14px; }

  .contact {
    position: absolute; right: 18px; top: 108px;
    list-style: none; text-align: right;
    color: var(--white); font-size: 10.5px; line-height: 16px;
  }
  .contact li { display: flex; justify-content: flex-end; align-items: center; gap: 7px; white-space: nowrap; }
  .contact svg { width: 10px; height: 10px; flex: none; }
  .contact .no-icon { padding-right: 17px; }
</style>
</head>
<body>
<main class="stage">

  <section class="card card-front" aria-label="Card front">
    <div class="brand"><span class="brand-mark"></span>Ledgerline Code Works</div>
  </section>

  <section class="card card-back" aria-label="Card back">
    <svg class="swoosh" viewBox="0 0 520 318" aria-hidden="true">
      <path d="M520,62 C446,68 362,96 332,160 C302,228 240,300 120,318 L520,318 Z" fill="var(--card-black)"/>
      <path d="M520,52 C438,58 350,86 318,152 C288,222 226,296 96,316" fill="none" stroke="var(--sky)" stroke-width="4"/>
      <path d="M520,58 C442,64 356,92 325,156 C295,226 233,298 108,318" fill="none" stroke="var(--sky-deep)" stroke-width="6"/>
    </svg>

    <div class="person">
      <div class="person-name">Greg Halvorsen</div>
      <div class="person-role">Managing Director</div>
    </div>

    <div class="brand"><span class="brand-mark"></span>Ledgerline Code Works</div>

    <ul class="contact">
      <li>+61 2 9387 4625
        <svg viewBox="0 0 10 10"><path d="M2 0.5 L4 2.5 L3 3.8 C3.8 5.4 4.6 6.2 6.2 7 L7.5 6 L9.5 8 L8 9.5 C4 9 1 6 0.5 2 Z" fill="var(--sky)"/></svg></li>
      <li>+61 4 1736 8490
        <svg viewBox="0 0 10 10"><rect x="2.5" y="0.5" width="5" height="9" rx="1" fill="var(--sky)"/><rect x="3.5" y="1.8" width="3" height="5.5" fill="var(--card-black)"/></svg></li>
      <li>gregh@lcw.net.au
        <svg viewBox="0 0 10 10"><rect x="0.5" y="2" width="9" height="6" fill="var(--sky)"/><path d="M0.5 2 L5 5.5 L9.5 2" fill="none" stroke="var(--card-black)" stroke-width="0.9"/></svg></li>
      <li>www.lcw.net.au
        <svg viewBox="0 0 10 10"><circle cx="5" cy="5" r="4.3" fill="var(--sky)"/><path d="M0.7 5 H9.3 M5 0.7 C3 3 3 7 5 9.3 M5 0.7 C7 3 7 7 5 9.3" fill="none" stroke="var(--card-black)" stroke-width="0.7"/></svg></li>
      <li>Suite 5 Level 8,
        <svg viewBox="0 0 10 10"><path d="M5 9.5 C3 6.5 1.8 5 1.8 3.4 A3.2 3.2 0 0 1 8.2 3.4 C8.2 5 7 6.5 5 9.5 Z" fill="var(--sky)"/><circle cx="5" cy="3.5" r="1.2" fill="var(--card-black)"/></svg></li>
      <li class="no-icon">147 Marlow Street</li>
      <li class="no-icon">Sydney NSW 2000</li>
    </ul>
  </section>

</main>
</body>
</html>
```